Velmoria-Quillmesh Partial Redesign - Web App

Are you able to apply your creativity to an existing layout? I’m convinced that even just a few touches can make a big difference to add personality and professionalism to a website design, and I’m looking for someone able to use existing ideas and bring them to the next level while keeping inside some given constraints.
The actual job is to improve an existing design concept and to apply it creatively to a landing page, a simple home page, and an older web app (single page website).
To help you start with a clear picture of the current situation and of my requirements, I created a detailed brief with screenshots, live examples, and complete instructions. You can find it attached to this job.
My tastes are inclined towards clean and simple designs. For this project I'm not looking for dazzling novelty, but for very solid craftsmanship. Are the right man - or woman - for the job?
Updates
I wanted to thank everybody who participated in this project. I made a choice, but also other designs were interesting. Hope to work with you another time.
Target Market(s)
Our main target is social media marketers and startuppers
Look and feel
Each slider illustrates characteristics of the customer's brand and the style your logo design should communicate.

```html
<!DOCTYPE html>
<html lang="en">
<head>
<meta charset="utf-8">
<title>Velmoria – Hashtag Insights</title>
<link rel="stylesheet" href="https://fonts.googleapis.com/css2?family=Arimo:wght@400;700&family=Roboto+Slab:wght@700&display=swap">
<style>
:root{
  --ink:#2f2f33;
  --muted:#555;
  --link:#1c5f9c;
  --brown:#b1705d;
  --brown-dark:#9a5a48;
  --slate:#343a42;
  --tan:#cbb994;
  --tan-text:#5b4f3b;
  --line:#dcdad0;
  --panel:#f4f4f4;
  --teal:#1f8a82;
  --teal-2:#2b9c92;
}
*{margin:0;padding:0;box-sizing:border-box}
html,body{width:1200px;height:1194px;overflow:hidden;background:#fff}
body{font-family:"Arimo",Arial,sans-serif;color:var(--ink)}
.stage{position:absolute;left:0;top:0;width:1420px;height:1413px;transform:scale(.84507);transform-origin:0 0}
.abs{position:absolute}
.header{left:0;top:0;width:1420px;height:107px;background:linear-gradient(#f3f3f3,#e4e4e4)}
.brand-dot{left:262px;top:34px;width:44px;height:44px;border-radius:50%;background:#3c3f46}
.brand-name{left:347px;top:30px;font:700 40px/1 "Arimo",sans-serif;color:#3c3f46}
.login{left:1072px;top:47px;font-size:12px;color:#222}
.nav{left:0;top:107px;width:1420px;height:54px;background:linear-gradient(#c08472,#a8644f);border-top:1px solid #cf9a8a}
.nav ul{list-style:none;display:flex;margin-left:210px;height:100%;border-left:1px solid #c98b7a}
.nav li{height:100%;display:flex;align-items:center;padding:0 23px;color:#fff;font-weight:700;font-size:14px;border-right:1px solid #c98b7a}
.stats{left:0;top:161px;width:1420px;height:111px;background:var(--slate)}
.stats-title{left:228px;top:181px;font:700 21px/25px "Roboto Slab",serif;color:#fff}
.count{top:178px;width:63px;height:53px;background:linear-gradient(#d9c79f,#c3ad80);border:2px solid #e2d4b3;border-radius:3px;font:700 26px/50px "Roboto Slab",serif;color:#3d3527;text-align:center}
.comma{top:216px;color:#c9b98f;font-size:16px}
.tweets-total{left:497px;top:244px;font-size:12px;color:#fff}
.divider{left:688px;top:182px;width:1px;height:70px;background:#4b525b}
.search{left:707px;top:195px;width:354px;height:44px;background:#fff;border:1px solid #ccc}
.search svg{position:absolute;left:14px;top:11px}
.search-btn{left:1072px;top:195px;width:104px;height:44px;background:var(--brown);color:#fff;font-weight:700;font-size:13px;line-height:44px;text-align:center;border:1px solid #c98b7a}
.panel{left:210px;top:330px;width:329px;height:729px;background:var(--panel)}
.mascot{left:216px;top:290px;width:60px;height:50px;border-radius:50%;background:radial-gradient(#6cc7ef,#2f9bd0)}
.panel-title{left:236px;top:311px;font:700 16px/1 "Roboto Slab",serif;color:#2b2b2b}
.tweet{left:226px;width:305px}
.avatar{position:absolute;left:0;top:0;width:54px;height:54px;border:1px solid #ddd;background:linear-gradient(#8b8b8b,#3d3d3d)}
.tweet-text{margin-left:61px;font-size:12px;line-height:18px;color:var(--ink)}
.tweet-text a{color:var(--link);text-decoration:none}
.tweet-time{margin-left:61px;margin-top:6px;font-size:12px;color:#333;display:flex;align-items:center;gap:6px}
.tweet-time i{display:inline-block;width:22px;height:12px;border-radius:6px;background:#bbb;margin-left:-28px}
.variants{left:584px;top:305px;font-size:15px;line-height:23px;color:#222}
.graph{left:540px;top:380px}
.toggle{left:1039px;top:1020px;width:171px;height:40px;display:flex;border:1px solid #166e67}
.toggle span{flex:1;display:flex;align-items:center;justify-content:center;color:#fff;font-weight:700;font-size:13px}
.toggle .on{background:var(--teal)}
.toggle .off{background:var(--teal-2);flex:1.25}
.inf-title{left:224px;top:1102px;font:700 15px/1 "Roboto Slab",serif;color:#2b2b2b}
.inf-list{left:224px;top:1133px;list-style:none;font-size:15px;line-height:30px;color:#333}
.scatter{left:585px;top:1080px}
.footer{left:0;top:1362px;width:1420px;height:51px;background:var(--slate)}
.foot-mark{left:222px;top:1374px;width:28px;height:28px;border-radius:50%;border:2px solid #6a6f77}
.copy{left:277px;top:1381px;font-size:12px;color:#e8e8e8}
.social{top:1377px;width:23px;height:23px;border-radius:3px}
</style>
</head>
<body>
<div class="stage">
  <header class="abs header"></header>
  <div class="abs brand-dot"></div>
  <div class="abs brand-name">Velmoria</div>
  <div class="abs login">Admin Login &nbsp;|&nbsp; Login</div>

  <nav class="abs nav"><ul>
    <li>HOME</li><li>ABOUT US</li><li>BLOG</li><li>SUMMARY</li><li>TIMELINE</li><li>INFLUENCERS</li><li>HASHTAGS</li>
  </ul></nav>

  <section class="abs stats"></section>
  <div class="abs stats-title">HASHTAGS<br>FOUND SO FAR</div>
  <div class="abs count" style="left:411px">11</div>
  <div class="abs comma" style="left:479px">,</div>
  <div class="abs count" style="left:489px">222</div>
  <div class="abs comma" style="left:557px">,</div>
  <div class="abs count" style="left:567px">333</div>
  <div class="abs tweets-total">IN 444,555,666 TWEETS</div>
  <div class="abs divider"></div>
  <div class="abs search">
    <svg width="22" height="22" viewBox="0 0 22 22"><circle cx="8" cy="8" r="6" fill="none" stroke="#999" stroke-width="2.5"/><line x1="12.5" y1="12.5" x2="19" y2="19" stroke="#999" stroke-width="3" stroke-linecap="round"/></svg>
  </div>
  <div class="abs search-btn">SEARCH</div>

  <aside class="abs panel"></aside>
  <div class="abs mascot" role="img" aria-label="Cartoon bird mascot"></div>
  <div class="abs panel-title">FOLLOW ME ON CHIRPLINE</div>

  <div class="abs tweet" style="top:353px"><div class="avatar" role="img" aria-label="User avatar photo"></div>
    <p class="tweet-text"><a>mirelpaz: #WhenIWasBataPa</a> , Trending at 1st Place Worldwide! ! Haha. Go for Pinoy <a>#Hashtags!</a> :'D</p>
    <div class="tweet-time"><i></i>3 minutes ago</div></div>
  <div class="abs tweet" style="top:450px"><div class="avatar" role="img" aria-label="User avatar artwork"></div>
    <p class="tweet-text"><a>TrailBackly</a>: RT @/Echo_Tagline2012Follow popular chirp #hashtags <a>http://lnk.qm/5StUJm9x</a></p>
    <div class="tweet-time"><i></i>13 minutes ago</div></div>
  <div class="abs tweet" style="top:551px"><div class="avatar" role="img" aria-label="User avatar photo"></div>
    <p class="tweet-text"><a>Echo_Tagline</a>: Follow popular chirp #hashtags <a>http://lnk.qm/Ltc2Yd1J</a></p>
    <div class="tweet-time"><i></i>15 minutes ago</div></div>
  <div class="abs tweet" style="top:651px"><div class="avatar" role="img" aria-label="User avatar photo"></div>
    <p class="tweet-text"><a>brivane</a>: Le saviez-vous ? Les tweets comprenant des #hashtags reçoivent 2 fois plus d'engagement autres <a>#Chirpline</a></p>
    <div class="tweet-time"><i></i>20 minutes ago</div></div>
  <div class="abs tweet" style="top:752px"><div class="avatar" role="img" aria-label="User avatar photo"></div>
    <p class="tweet-text"><a>mirelpaz: #WhenIWasBataPa</a> , Trending at 1st Place Worldwide! ! Haha. Go for Pinoy <a>#Hashtags!</a> :'D</p>
    <div class="tweet-time"><i></i>3 minutes ago</div></div>
  <div class="abs tweet" style="top:849px"><div class="avatar" role="img" aria-label="User avatar artwork"></div>
    <p class="tweet-text"><a>TrailBackly</a>: RT @/Echo_Tagline2012Follow popular chirp #hashtags <a>http://lnk.qm/5StUJm9x</a></p>
    <div class="tweet-time"><i></i>13 minutes ago</div></div>
  <div class="abs tweet" style="top:961px"><div class="avatar" role="img" aria-label="User avatar photo"></div>
    <p class="tweet-text"><a>Echo_Tagline</a>: Follow popular chirp #hashtags <a>http://lnk.qm/Ltc2Yd1J</a></p>
    <div class="tweet-time"><i></i>15 minutes ago</div></div>

  <div class="abs variants">Variants: hashtags:80% Hashtags:14% HASHTAGS:3% HashTags:3% hashTags:0%<br>Popularity: 57.7</div>

  <svg class="abs graph" width="690" height="630" viewBox="540 380 690 630" font-family="Arimo, sans-serif" font-size="12" fill="#5b4f3b" text-anchor="middle">
    <g stroke="#dcdad0" stroke-width="3">
      <line x1="864" y1="699" x2="723" y2="473"/><line x1="864" y1="699" x2="895" y2="443"/>
      <line x1="864" y1="699" x2="1089" y2="485"/><line x1="864" y1="699" x2="609" y2="610"/>
      <line x1="864" y1="699" x2="1034" y2="646"/><line x1="864" y1="699" x2="1160" y2="764"/>
      <line x1="864" y1="699" x2="632" y2="781"/><line x1="864" y1="699" x2="874" y2="903"/>
      <line x1="864" y1="699" x2="1043" y2="928"/><line x1="864" y1="699" x2="706" y2="949"/>
    </g>
    <g fill="#cbb994">
      <circle cx="723" cy="473" r="49"/><circle cx="895" cy="443" r="49"/><circle cx="1089" cy="485" r="49"/>
      <circle cx="609" cy="610" r="49"/><circle cx="1034" cy="646" r="49"/><circle cx="1160" cy="764" r="49"/>
      <circle cx="632" cy="781" r="49"/><circle cx="874" cy="903" r="35"/><circle cx="1043" cy="928" r="49"/>
      <circle cx="706" cy="949" r="47"/><circle cx="864" cy="699" r="42"/>
    </g>
    <text x="723" y="478">YOU</text><text x="895" y="448">WHERE</text><text x="1089" y="490">WHEN</text>
    <text x="609" y="615">SHE</text><text x="1034" y="651">ME</text><text x="1160" y="769">PEOPLE</text>
    <text x="632" y="786">EVERYTHING</text><text x="874" y="908">TO</text><text x="1043" y="933">SHOULD</text>
    <text x="706" y="954">TAG</text><text x="864" y="704">HASHTAG</text>
  </svg>

  <div class="abs toggle"><span class="on">SIMPLE</span><span class="off">ADVANCED</span></div>

  <h2 class="abs inf-title">THE TOP 6 INFULENCERS FOR #TAG</h2>
  <ol class="abs inf-list">
    <li>1. Support</li><li>2. Torvenhale</li><li>3. KDRenko</li><li>4. Stillroamingon</li><li>5. Joelmarsten</li><li>6. Rio_Calderon</li>
  </ol>

  <svg class="abs scatter" width="560" height="260" viewBox="585 1080 560 260" font-family="Arimo, sans-serif" font-size="12" fill="#333">
    <g stroke="#dcdad0" stroke-width="3" fill="none">
      <polyline points="611,1098 611,1317 1110,1317"/>
    </g>
    <polygon points="611,1085 603,1102 619,1102" fill="#dcdad0"/>
    <polygon points="1122,1317 1104,1309 1104,1325" fill="#dcdad0"/>
    <g fill="#cbb994" stroke="#fff" stroke-width="2">
      <circle cx="639" cy="1142" r="27"/><circle cx="669" cy="1118" r="27"/>
      <circle cx="638" cy="1205" r="27"/><circle cx="663" cy="1228" r="27"/>
      <circle cx="697" cy="1252" r="27"/><circle cx="659" cy="1278" r="27"/>
    </g>
    <text x="993" y="1335" text-anchor="middle">User specializtion for this hashtag</text>
    <text transform="translate(602 1211) rotate(-90)" text-anchor="middle">User influence for this hashtag</text>
  </svg>

  <footer class="abs footer"></footer>
  <div class="abs foot-mark"></div>
  <div class="abs copy">Copyright © &nbsp;-2012 Velmoria Ltd All Right Resevered</div>
  <div class="abs social" style="left:1154px;background:#3b5b9a"></div>
  <div class="abs social" style="left:1184px;background:#3fa9dc"></div>
</div>
</body>
</html>
```